we are an outdoor outlet in a country club that has a variety of outlets. The Club is called Meadowlark and is located in Cairo, Egypt. This garden menu will include cuisines from the Mediterranean, Asia and Texmex. we need a menu that is colorful and would fit an A3 size, back and front are to be used. Attached is the old menu currently in use (Garden Menu 2012.pdf is just for reference) and the new menu text for you to use is under the name Garden Menu Fall 2013
thank you.
Updates
Logo files have been uploaded for this project
Industry/Entity Type
Club
Look and feel
Each slider illustrates characteristics of the customer's brand and the style your logo design should communicate.

```html
<!DOCTYPE html>
<html lang="en">
<head>
<meta charset="utf-8">
<title>Meadowlark Garden Menu – Fall 2013</title>
<link href="https://fonts.googleapis.com/css2?family=Great+Vibes&family=Dancing+Script:wght@500;700&family=Open+Sans:wght@400;600&display=swap" rel="stylesheet">
<style>
  :root {
    --bg: #ece9e4;
    --paper: #ffffff;
    --band: #dcd9d3;
    --magenta: #a8285d;
    --lime: #bfcf3f;
    --lime-soft: #e3e9b0;
    --olive: #6e7a28;
    --teal: #3b8a9c;
    --brown: #5a2430;
    --muted: #8a8080;
    --faint: #efedea;
  }
  * { box-sizing: border-box; margin: 0; padding: 0; }
  html, body { width: 1200px; height: 800px; overflow: hidden; background: var(--bg); }
  body { font-family: "Open Sans", sans-serif; color: var(--brown); position: relative; }

  .menu-sheet {
    position: absolute; left: 20px; width: 1160px; height: 375px;
    background: var(--paper); display: grid; grid-template-columns: 1fr 14px 1fr;
    box-shadow: 0 2px 10px rgba(0,0,0,.08); overflow: hidden;
  }
  .sheet-front { top: 15px; }
  .sheet-back { top: 408px; }
  .panel { position: relative; overflow: hidden; }
  .divider { position: relative; }
  .divider::before { content: ""; position: absolute; left: 6px; top: 14px; bottom: 14px; border-left: 2px solid var(--magenta); opacity: .45; }

  /* shared type */
  .section-heading { font-family: "Great Vibes", cursive; color: var(--olive); font-size: 34px; line-height: 1; }
  .swash { display: block; margin-top: 1px; }
  .sub-heading { font-family: "Dancing Script", cursive; font-weight: 700; font-size: 17px; line-height: 1.2; color: var(--teal); margin: 4px 0 3px; }
  .sub-heading.magenta { color: var(--magenta); }
  .sub-heading.olive { color: var(--olive); }
  .item { display: grid; grid-template-columns: 1fr auto; column-gap: 6px; margin-bottom: 4px; }
  .item-name { font-family: "Dancing Script", cursive; font-weight: 700; font-size: 13.5px; line-height: 1.2; color: var(--brown); }
  .item-desc { grid-column: 1; font-size: 8px; color: var(--muted); line-height: 1.3; }
  .item-price { grid-row: 1; grid-column: 2; font-size: 8px; color: var(--muted); align-self: center; }
  .bullets { list-style: none; }
  .bullets li { font-family: "Dancing Script", cursive; font-weight: 700; font-size: 13px; line-height: 1.5; display: flex; gap: 5px; }
  .bullets li::before { content: "•"; color: var(--magenta); }
  .bullets li span:first-child { flex: 1; }
  .bullets .price { font-family: "Open Sans", sans-serif; font-weight: 400; font-size: 8px; color: var(--muted); align-self: center; }
  .brand-name { font-weight: 600; font-size: 13px; color: var(--brown); display: inline-flex; align-items: center; gap: 5px; }
  .brand-name .dot { width: 8px; height: 8px; background: var(--olive); border-radius: 50%; }
  .footnote { position: absolute; left: 20px; right: 20px; bottom: 8px; font-size: 8px; color: var(--muted); text-align: center; }

  /* front – Mediterranean */
  .header-band { height: 92px; background: var(--band); display: flex; }
  .header-art {
    width: 300px; height: 100%;
    background: radial-gradient(circle at 18% 50%, var(--magenta) 0 30px, transparent 32px),
                radial-gradient(circle at 48% 40%, var(--lime) 0 24px, transparent 26px),
                radial-gradient(circle at 74% 58%, #9c9893 0 26px, transparent 28px),
                linear-gradient(120deg, #d6d3cd, #cfccc5);
  }
  .header-brand { flex: 1; padding: 10px 18px 0 8px; text-align: right; }
  .menu-title { font-family: "Great Vibes", cursive; color: var(--magenta); font-size: 27px; font-weight: 400; line-height: 1; margin-top: 6px; }
  .med-body { display: grid; grid-template-columns: 1fr 250px; height: 283px; }
  .med-left { padding: 8px 14px 0 22px; }
  .appetizers { background: var(--lime-soft); padding: 6px 14px 0 14px; position: relative; }
  .appetizer-art { position: absolute; right: 0; bottom: 0; width: 60px; height: 60px;
    background: radial-gradient(circle at 50% 50%, #9aa83a 0 18px, transparent 20px); }
  .med-right { display: grid; grid-template-columns: 1fr 1fr 1fr; column-gap: 16px; padding: 12px 18px 0; position: relative; }
  .right-art { position: absolute; right: -40px; top: -40px; width: 200px; height: 200px;
    background: radial-gradient(circle, var(--faint) 0 55%, transparent 70%); }
  .med-right > div { position: relative; }

  /* back – Asian & Tex-Mex */
  .art-strip { height: 62px; }
  .asian-art { background: radial-gradient(circle at 14% 55%, var(--magenta) 0 20px, transparent 22px),
                          radial-gradient(ellipse at 32% 45%, #b7c46a 0 36px, transparent 38px),
                          linear-gradient(90deg, #e4e1dc, #d8d5cf); }
  .texmex-art { background: radial-gradient(circle at 80% 50%, #c27a93 0 22px, transparent 24px),
                           radial-gradient(ellipse at 58% 50%, #c9d27a 0 30px, transparent 32px),
                           linear-gradient(90deg, #d8d5cf, #e4e1dc); }
  .corner-title { padding: 6px 22px 0; display: flex; align-items: flex-end; justify-content: space-between; }
  .back-columns { display: grid; grid-template-columns: 1fr 1fr; column-gap: 22px; padding: 4px 22px 0; }
  .texmex-columns { grid-template-columns: 1fr 1fr 1fr; column-gap: 16px; }
</style>
</head>
<body>

<!-- front sheet -->
<main class="menu-sheet sheet-front">
  <section class="panel">
    <header class="header-band">
      <div class="header-art" role="img" aria-label="Illustration of stylised garden flowers and leaves in magenta, lime and grey"></div>
      <div class="header-brand">
        <div class="brand-name"><span class="dot"></span>Meadowlark</div>
        <h1 class="menu-title">Garden Menu<br>Fall 2013</h1>
      </div>
    </header>
    <div class="med-body">
      <div class="med-left">
        <h2 class="section-heading">Mediterranean Corner</h2>
        <svg class="swash" width="200" height="10" viewBox="0 0 200 10"><path d="M2 7 Q55 0 100 5 T198 3" stroke="var(--magenta)" stroke-width="2" fill="none"/></svg>
        <h3 class="sub-heading magenta">Soups</h3>
        <div class="item"><span class="item-name">Tomato Basil</span><span class="item-price">LE 00.00</span><span class="item-desc">Roasted tomatoes simmered with basil and cream</span></div>
        <div class="item"><span class="item-name">Chicken Cream</span><span class="item-price">LE 00.00</span><span class="item-desc">Creamy chicken broth with tender chicken</span></div>
        <div class="item"><span class="item-name">Minestrone</span><span class="item-price">LE 00.00</span><span class="item-desc">Seasonal vegetables, beans and pasta</span></div>
      </div>
      <section class="appetizers">
        <div class="appetizer-art" role="img" aria-label="Illustration of a round green garden blossom"></div>
        <h3 class="sub-heading">Appetizers</h3>
        <ul class="bullets">
          <li><span>Stuffed vine leaves</span><span class="price">LE 00.00</span></li>
          <li><span>Grilled halloumi with mint</span><span class="price">LE 00.00</span></li>
          <li><span>Hummus with pita bread</span><span class="price">LE 00.00</span></li>
          <li><span>Baba ghanoush</span><span class="price">LE 00.00</span></li>
          <li><span>Falafel with tahini</span><span class="price">LE 00.00</span></li>
          <li><span>Fried calamari with aioli</span><span class="price">LE 00.00</span></li>
          <li><span>Marinated olives and feta</span><span class="price">LE 00.00</span></li>
          <li><span>Spinach fatayer</span><span class="price">LE 00.00</span></li>
        </ul>
      </section>
    </div>
  </section>

  <div class="divider" aria-hidden="true"></div>

  <section class="panel med-right">
    <div class="right-art" role="img" aria-label="Faint outline illustration of a large white flower"></div>
    <div>
      <h3 class="sub-heading olive">Salads</h3>
      <div class="item"><span class="item-name">Caprese</span><span class="item-price">LE 00.00</span><span class="item-desc">Mozzarella, tomato and basil</span></div>
      <div class="item"><span class="item-name">Greek Salad</span><span class="item-price">LE 00.00</span><span class="item-desc">Feta, olives, cucumber and onion</span></div>
      <div class="item"><span class="item-name">Fattoush</span><span class="item-price">LE 00.00</span><span class="item-desc">Crisp greens and toasted pita</span></div>
      <div class="item"><span class="item-name">Tabbouleh</span><span class="item-price">LE 00.00</span><span class="item-desc">Parsley, bulgur, lemon and mint</span></div>
    </div>
    <div>
      <h3 class="sub-heading">Pizza &amp; Pasta</h3>
      <div class="item"><span class="item-name">Pizza Margherita</span><span class="item-price">LE 00.00</span><span class="item-desc">Tomato, mozzarella and basil</span></div>
      <div class="item"><span class="item-name">Create your own pasta</span><span class="item-price">LE 00.00</span><span class="item-desc">Penne, spaghetti or fusilli</span></div>
      <div class="item"><span class="item-name">Lasagna</span><span class="item-price">LE 00.00</span><span class="item-desc">Beef ragù with béchamel</span></div>
      <h3 class="sub-heading magenta">Toppings</h3>
      <ul class="bullets">
        <li><span>Peppers, olives, onion</span></li>
        <li><span>Mushroom, chicken, tuna</span></li>
        <li><span>Smoked salmon, shrimp</span></li>
      </ul>
    </div>
    <div>
      <h3 class="sub-heading">Sandwiches</h3>
      <div class="item"><span class="item-name">Beef shawarma</span><span class="item-price">LE 00.00</span></div>
      <div class="item"><span class="item-name">Grilled kofta wrap</span><span class="item-price">LE 00.00</span></div>
      <div class="item"><span class="item-name">Tuna pita, tzatziki</span><span class="item-price">LE 00.00</span></div>
      <div class="item"><span class="item-name">Turkey club</span><span class="item-price">LE 00.00</span></div>
      <h3 class="sub-heading">Main Courses</h3>
      <div class="item"><span class="item-name">Veal Parmigiana</span><span class="item-price">LE 00.00</span><span class="item-desc">With tomato and cheese</span></div>
      <div class="item"><span class="item-name">Chicken Saltimbocca</span><span class="item-price">LE 00.00</span><span class="item-desc">With sage and white wine</span></div>
      <div class="item"><span class="item-name">Moroccan Chicken</span><span class="item-price">LE 00.00</span><span class="item-desc">Spiced, with couscous</span></div>
    </div>
    <p class="footnote">Prices are subject to service charge and taxes</p>
  </section>
</main>

<!-- back sheet -->
<main class="menu-sheet sheet-back">
  <section class="panel">
    <div class="art-strip asian-art" role="img" aria-label="Illustration of leaves, a blossom and pale bamboo stems"></div>
    <div class="corner-title">
      <div>
        <h2 class="section-heading">Asian Corner</h2>
        <svg class="swash" width="160" height="10" viewBox="0 0 160 10"><path d="M2 7 Q45 0 80 5 T158 3" stroke="var(--magenta)" stroke-width="2" fill="none"/></svg>
      </div>
      <div class="brand-name"><span class="dot"></span>Meadowlark</div>
    </div>
    <div class="back-columns">
      <div>
        <h3 class="sub-heading magenta">Salads &amp; Appetizers</h3>
        <div class="item"><span class="item-name">Chicken Wonton Salad</span><span class="item-price">LE 00.00</span><span class="item-desc">Crisp wontons, greens and sesame dressing</span></div>
        <div class="item"><span class="item-name">Chicken Sesame Noodle Salad</span><span class="item-price">LE 00.00</span><span class="item-desc">Egg noodles, peanuts and ginger soy</span></div>
        <div class="item"><span class="item-name">Spring Rolls</span><span class="item-price">LE 00.00</span><span class="item-desc">Vegetable rolls with sweet chili sauce</span></div>
        <div class="item"><span class="item-name">Indian Samosas</span><span class="item-price">LE 00.00</span><span class="item-desc">Spiced potato and peas with mint chutney</span></div>
      </div>
      <div>
        <h3 class="sub-heading olive">Main Courses</h3>
        <div class="item"><span class="item-name">Murgh Chicken Makhani</span><span class="item-price">LE 00.00</span><span class="item-desc">Butter chicken with basmati rice</span></div>
        <div class="item"><span class="item-name">Chicken Tandoori</span><span class="item-price">LE 00.00</span><span class="item-desc">Yogurt marinated, served with naan</span></div>
        <div class="item"><span class="item-name">Thai Coconut Curry Shrimp</span><span class="item-price">LE 00.00</span><span class="item-desc">Red curry, coconut milk and jasmine rice</span></div>
        <div class="item"><span class="item-name">Mongolian Beef</span><span class="item-price">LE 00.00</span><span class="item-desc">Wok-fried beef with spring onion</span></div>
      </div>
    </div>
  </section>

  <div class="divider" aria-hidden="true"></div>

  <section class="panel">
    <div class="art-strip texmex-art" role="img" aria-label="Illustration of cacti and a blossom in soft grey, lime and rose"></div>
    <div class="corner-title">
      <div>
        <h2 class="section-heading">Tex-Mex</h2>
        <svg class="swash" width="120" height="10" viewBox="0 0 120 10"><path d="M2 7 Q35 0 60 5 T118 3" stroke="var(--magenta)" stroke-width="2" fill="none"/></svg>
      </div>
    </div>
    <div class="back-columns texmex-columns">
      <div>
        <h3 class="sub-heading">Salads</h3>
        <div class="item"><span class="item-name">Taco Salad</span><span class="item-price">LE 00.00</span><span class="item-desc">Beef, beans, cheese and tortilla bowl</span></div>
        <div class="item"><span class="item-name">Caesar Salad</span><span class="item-price">LE 00.00</span><span class="item-desc">Romaine, croutons and parmesan</span></div>
        <div class="item"><span class="item-name">Southwest Salad</span><span class="item-price">LE 00.00</span><span class="item-desc">Corn, black beans and lime</span></div>
      </div>
      <div>
        <h3 class="sub-heading magenta">Appetizers</h3>
        <ul class="bullets">
          <li><span>Nachos with cheese</span><span class="price">LE 00.00</span></li>
          <li><span>Guacamole and chips</span><span class="price">LE 00.00</span></li>
          <li><span>Buffalo wings</span><span class="price">LE 00.00</span></li>
          <li><span>Jalapeño poppers</span><span class="price">LE 00.00</span></li>
          <li><span>Potato skins</span><span class="price">LE 00.00</span></li>
        </ul>
      </div>
      <div>
        <h3 class="sub-heading olive">Main Courses &amp; Sandwiches</h3>
        <div class="item"><span class="item-name">Fajitas</span><span class="item-price">LE 00.00</span><span class="item-desc">Chicken or beef with tortillas</span></div>
        <div class="item"><span class="item-name">Beef Burrito</span><span class="item-price">LE 00.00</span><span class="item-desc">Rice, beans and salsa</span></div>
        <div class="item"><span class="item-name">Chicken Quesadilla</span><span class="item-price">LE 00.00</span><span class="item-desc">With sour cream</span></div>
        <div class="item"><span class="item-name">Beef Burger</span><span class="item-price">LE 00.00</span><span class="item-desc">With fries and coleslaw</span></div>
      </div>
    </div>
    <p class="footnote">Prices are subject to service charge and taxes</p>
  </section>
</main>
</body>
</html>
```